A business card design for a dental office. We have Two doctors working here. We practice general de

I already have a logo designed for the office with the name and a slogan.
Now I need to create design for a business card using the same logo.
Details Needed on the front side of the card are :
Bernard K. Oswin, DDS
Gerald M Fenwick, DDS
418 Birch Lane
Portland, CT 00000
Phone : 555 019 4831
Fax : 555 019 4832
Website : WWW.BrightmoorToothHaven.Com
Office hours by appointment
On the back side of the card need :
Appointment
Date....................Time...................
With....................................
If unable to keep your appointment, please give 24-48 hours notice in order to avoid broken appointment fee.

Industry/Entity Type

Dental Clinic

Contact Information for Business Card

Bernard K. Oswin, DDS
Gerald M Fenwick, DDS
418 Birch Lane
Portland, CT 00000
Phone : 555 019 4831
Fax : 555 019 4832
Appointment

Requirements
Must have
• Keep the Name and slogan on the logo on the front of the card. You can move them around the Logo and Name/Slogan of business (Oswin Family Dentistry/We give you reasons to smile) as you wish to get a feel of the design.
• Bernard K. Oswin, DDS
• Gerald M Fenwick, DDS
• 418 Birch Lane
• Portland, CT 00000
• Phone : 555 019 4831
• Fax : 555 019 4832
• WWW.BrightmoorToothHaven.Com
• Keep these three groups above as they are together now in different areas of the front side.
• On the back side of the card need :
• Appointment
• Date....................Time...................
• With....................................
• If unable to keep your appointment, please give 24-48 hours notice in order to avoid broken appointment fee.

```html
<!DOCTYPE html>
<html lang="en">
<head>
<meta charset="utf-8">
<title>Oswin Family Dentistry – Business Card</title>
<link href="https://fonts.googleapis.com/css2?family=Source+Sans+3:ital,wght@0,400;0,600;0,700;1,600&display=swap" rel="stylesheet">
<style>
  :root {
    --teal: #14a98f;
    --teal-dark: #0f9a82;
    --navy: #1a4fa0;
    --ink: #1d1d1d;
    --paper: #ffffff;
    --backdrop: #e9e7e4;
  }
  * { margin: 0; padding: 0; box-sizing: border-box; }
  html, body { width: 1200px; height: 900px; overflow: hidden; }
  body {
    background: var(--backdrop);
    font-family: "Source Sans 3", "Myriad Pro", Arial, sans-serif;
    color: var(--ink);
    position: relative;
  }
  .card {
    position: absolute;
    background: var(--paper);
    border-radius: 18px;
    overflow: hidden;
    box-shadow: 0 6px 22px rgba(0,0,0,0.12);
  }
  .band { position: absolute; left: 0; right: 0; background: var(--teal); }
  .emblem {
    position: absolute;
    border-radius: 50%;
    background: var(--paper);
    border: 6px solid var(--paper);
    box-shadow: 0 0 0 2px var(--teal-dark) inset;
  }

  /* Front */
  .card-front { left: 78px; top: 34px; width: 588px; height: 364px; }
  .card-front .band { top: 28px; height: 100px; }
  .card-front .emblem { left: 234px; top: 4px; width: 132px; height: 132px; }
  .practice-name {
    position: absolute; left: 0; right: 0; top: 166px;
    text-align: center;
    color: var(--navy);
    font-weight: 700;
    font-size: 25px;
    letter-spacing: 1.5px;
    text-transform: uppercase;
  }
  .contact-list {
    position: absolute; right: 318px; top: 242px;
    list-style: none; text-align: right;
    font-size: 17px; line-height: 24.7px;
  }
  .contact-list svg { width: 12px; height: 12px; margin-left: 8px; vertical-align: -1px; fill: var(--teal); }
  .contact-list .hours { color: var(--teal); font-style: italic; font-weight: 600; font-size: 19px; margin-right: 0; }
  .doctors { position: absolute; left: 307px; top: 241px; }
  .doctor { color: var(--teal); font-weight: 600; font-size: 23px; line-height: 25px; }
  .doctor small { font-size: 17px; }
  .address { font-size: 17px; line-height: 24.7px; margin-top: 2px; }

  /* Back */
  .card-back { left: 389px; top: 506px; width: 565px; height: 350px; }
  .card-back .band { top: 26px; height: 96px; }
  .card-back .emblem { left: 239px; top: 8px; width: 122px; height: 122px; }
  .appt-title {
    position: absolute; left: 0; right: 0; top: 146px;
    text-align: center; color: var(--teal); font-weight: 600; font-size: 23px;
  }
  .appt-field {
    position: absolute; color: var(--teal); font-weight: 600; font-size: 18px;
    display: flex; align-items: baseline;
  }
  .appt-field .rule { border-bottom: 2px dotted var(--ink); height: 1px; margin-left: 10px; }
  .appt-note {
    position: absolute; left: 0; right: 0; top: 286px;
    text-align: center; color: var(--teal); font-weight: 600; font-size: 16px; line-height: 21px;
  }
</style>
</head>
<body>

<section class="card card-front">
  <div class="band"></div>
  <div class="emblem"></div>
  <h1 class="practice-name">Oswin Family Dentistry</h1>

  <ul class="contact-list">
    <li>555 019 4831<svg viewBox="0 0 12 12"><path d="M2.5 1l2 2-1 1.5c.6 1.5 1.7 2.6 3 3.2l1.5-1 2 2-1.3 1.8C5 10 2 7 .9 2.3z"/></svg></li>
    <li>555 019 4832<svg viewBox="0 0 12 12"><path d="M1 4h10v7H1zM3 1h6v3H3z"/></svg></li>
    <li>WWW.BrightmoorToothHaven.Com<svg viewBox="0 0 12 12"><circle cx="6" cy="6" r="5.5"/></svg></li>
    <li class="hours">Office hours by appointment</li>
  </ul>

  <div class="doctors">
    <p class="doctor">Bernard K. Oswin, <small>DDS</small></p>
    <p class="doctor">Gerald M Fenwick, <small>DDS</small></p>
    <p class="address">418 Birch Lane<br>Portland, CT 00000</p>
  </div>
</section>

<section class="card card-back">
  <div class="band"></div>
  <div class="emblem"></div>
  <h2 class="appt-title">Appointment</h2>
  <div class="appt-field" style="left:84px; top:206px;">Date<span class="rule" style="width:126px"></span></div>
  <div class="appt-field" style="left:276px; top:206px;">Time<span class="rule" style="width:148px"></span></div>
  <div class="appt-field" style="left:86px; top:249px;">With<span class="rule" style="width:342px"></span></div>
  <p class="appt-note">If unable to keep your appointment, please give 24-48 hours<br>notice in order to avoid broken appointment fee.</p>
</section>

</body>
</html>
```